Natural Light/Organic/Documentary Photography Business

I like a simple, approachable, feminine, earthy/organic feel. Earth/neutral tones, nothing too loud or obnoxious. I like the watercolor look. I don't want anything too trendy or something I'll get tired of after a couple months. As far as colors, I am much more a fan of cream/taupe/blue/green...not a fan of pink or purple at all.

Target Market(s)

Weddings & Families

Industry/Entity Type

Wedding Photography

Contact Information for Business Card

website, email, phone number

Font styles to use
Other font styles liked:
• Horizontes, Gotham

Colors

Designer to choose colors to be used in the design.

Requirements
Must have
• Website: www.mirelhatchway.com
• Phone: 418.629.5073
• Email: mirel@mirelhatchway.com
Nice to have
• I like the watercolor look but its not necessary. I like simple/earthy tones. Nothing too loud or distracting. Simple & feminine without being too girly. I like an approachable/soft feel.
• Instagram: www.instagram.com/mirelhatchwayphotography/
Should not have
• NO loud colors or design or pattern. I do not want a photo of a camera or lens or anything cheesy like that.

```html
<!DOCTYPE html>
<html lang="en">
<head>
<meta charset="utf-8">
<title>Mirel Hatchway Photography – Business Card</title>
<link rel="stylesheet" href="https://fonts.googleapis.com/css2?family=Source+Sans+3:wght@400;600&display=swap">
<style>
  :root {
    --page-bg: #ebebeb;
    --card-bg: #1c1c1c;
    --taupe: #8b7d73;
    --taupe-muted: #74685f;
    --ink-light: #ffffff;
    --icon-grey: #9a9a9a;
    --divider: #6f6862;
  }
  * { margin: 0; padding: 0; box-sizing: border-box; }
  html, body {
    width: 1200px;
    height: 799px;
    overflow: hidden;
    background: var(--page-bg);
    font-family: "Source Sans 3", "Myriad Pro", Arial, sans-serif;
  }
  .canvas {
    position: relative;
    width: 1200px;
    height: 799px;
  }
  .card {
    position: absolute;
    left: 313px;
    width: 584px;
    height: 333px;
    background: var(--card-bg);
  }
  .card--front { top: 51px; }
  .card--back { top: 413px; }

  /* Front */
  .brand-mark {
    position: absolute;
    font-weight: 400;
    white-space: nowrap;
    transform: translate(-50%, -50%);
  }
  .card--front .brand-mark {
    left: 164px;
    top: 167px;
    font-size: 24px;
    color: var(--taupe-muted);
    letter-spacing: 0.5px;
  }
  .divider {
    position: absolute;
    left: 292px;
    top: 105px;
    width: 1px;
    height: 119px;
    background: var(--divider);
  }
  .contact {
    position: absolute;
    left: 314px;
    top: 108px;
  }
  .contact__name {
    font-size: 21px;
    font-weight: 600;
    color: var(--taupe);
    line-height: 1;
    margin-bottom: 13px;
    letter-spacing: 0.2px;
  }
  .contact__list { list-style: none; }
  .contact__item {
    display: flex;
    align-items: center;
    height: 19px;
    font-size: 15px;
    color: var(--ink-light);
    line-height: 1;
  }
  .contact__icon {
    width: 12px;
    height: 12px;
    margin: 0 10px 0 8px;
    flex: none;
  }

  /* Back */
  .card--back .brand-mark {
    left: 292px;
    top: 165px;
    font-size: 42px;
    color: var(--ink-light);
    letter-spacing: 1px;
  }
  .card--back .site {
    position: absolute;
    left: 0;
    right: 0;
    top: 278px;
    text-align: center;
    font-size: 15px;
    color: var(--ink-light);
    letter-spacing: 3.6px;
  }
</style>
</head>
<body>
<main class="canvas">

  <section class="card card--front" aria-label="Business card front">
    <div class="brand-mark">Mirel Hatchway</div>
    <div class="divider"></div>
    <div class="contact">
      <p class="contact__name">Mirel Hatchway</p>
      <ul class="contact__list">
        <li class="contact__item">
          <svg class="contact__icon" viewBox="0 0 12 12" aria-hidden="true">
            <path d="M1 4 Q6 0 11 4 L9.5 5.5 L8 4.5 L8 3.5 Q6 2.8 4 3.5 L4 4.5 L2.5 5.5 Z" fill="var(--icon-grey)"/>
            <rect x="2.5" y="6" width="7" height="5" rx="1" fill="var(--icon-grey)"/>
          </svg>
          418.629.5073
        </li>
        <li class="contact__item">
          <svg class="contact__icon" viewBox="0 0 12 12" aria-hidden="true">
            <rect x="0.5" y="2.5" width="11" height="7.5" fill="var(--icon-grey)"/>
            <path d="M0.5 2.5 L6 7 L11.5 2.5" fill="none" stroke="var(--card-bg)" stroke-width="1"/>
          </svg>
          mirel@mirelhatchway.com
        </li>
        <li class="contact__item">
          <svg class="contact__icon" viewBox="0 0 12 12" aria-hidden="true">
            <circle cx="6" cy="6" r="5.5" fill="var(--icon-grey)"/>
            <path d="M6 0.5 V11.5 M0.5 6 H11.5 M6 0.5 Q2.5 6 6 11.5 M6 0.5 Q9.5 6 6 11.5" fill="none" stroke="var(--card-bg)" stroke-width="0.8"/>
          </svg>
          www.mirelhatchway.com
        </li>
        <li class="contact__item">
          <svg class="contact__icon" viewBox="0 0 12 12" aria-hidden="true">
            <rect x="1" y="1" width="10" height="10" rx="1.5" fill="var(--icon-grey)"/>
          </svg>
          mirelhatchwayphotography
        </li>
      </ul>
    </div>
  </section>

  <section class="card card--back" aria-label="Business card back">
    <div class="brand-mark">Mirel Hatchway</div>
    <p class="site">WWW.MIRELHATCHWAY.COM</p>
  </section>

</main>
</body>
</html>
```